Corvane Business Cards

Front of business card will have logo, name, address, & telephone number. Back of card will have a list of services provided - Roads, Substation Pads, Temporary Pads, Site Pads, Land Leveling, Powerline Row Cleaning, Land Clearing, Gates, Fencing, Construction Entrances, Excavation, Trenching, Underground Utilities, Directional Boring, Pile Driving. We are a construction company that uses heavy equipment like bulldozers, motor graders/blades, dump trucks, backhoes, hydro axes, & skid loaders. We build roads, pads, & install electric utility lines & waterlines underground. This logo is new. The word "Construction" can be smaller as uploaded 2 example edited logos. We will be using this card design for many employees.
Target Market(s)
Industrial Electric Powerline, Wind Turbine, Solar Panel, & Water Utility companies.
Contact Information for Business Card
Name/Position - Dwayne Halster - Owner
Address: 4875 FM 309
Merkel, TX 79412
Phone number - (325) 482-5096

```html
<!DOCTYPE html>
<html lang="en">
<head>
<meta charset="utf-8">
<title>Corvane Construction – Business Card</title>
<link href="https://fonts.googleapis.com/css2?family=Oswald:wght@500&family=Poppins:wght@400;500&display=swap" rel="stylesheet">
<style>
  :root {
    --backdrop: #9c9c9e;
    --card-light: #e8e8eb;
    --maroon: #3b0d17;
    --maroon-deep: #2f0a12;
    --ink: #3a3035;
    --ink-soft: #4a4448;
    --paper: #ecebee;
    --rule-light: #b9b0b3;
  }
  * { box-sizing: border-box; margin: 0; padding: 0; }
  html, body { width: 1105px; height: 1200px; overflow: hidden; }
  body { background: var(--backdrop); position: relative; font-family: "Poppins", sans-serif; }

  .card { position: absolute; left: 182px; width: 746px; height: 425px; }

  /* Front */
  .card-front { top: 119px; background: var(--card-light); }
  .identity { position: absolute; right: 424px; top: 172px; text-align: right; white-space: nowrap; }
  .identity-name { font-family: "Oswald", sans-serif; font-weight: 500; font-size: 40px; line-height: 1; color: var(--maroon); letter-spacing: 0.5px; }
  .identity-role { font-size: 17px; line-height: 1.2; color: var(--ink-soft); margin-top: 4px; }
  .identity-rule { position: absolute; left: 346px; top: 175px; width: 2px; height: 62px; background: var(--maroon); }
  .contact-list { position: absolute; left: 369px; top: 174px; list-style: none; }
  .contact-list li { display: flex; align-items: center; gap: 8px; height: 21.5px; font-size: 17.5px; color: var(--ink-soft); white-space: nowrap; }
  .contact-list svg { width: 13px; height: 13px; fill: var(--ink); flex: none; }
  .address-band { position: absolute; left: 0; right: 0; top: 362px; height: 38px; background: var(--maroon); color: var(--paper); }
  .address { position: absolute; left: 363px; top: 50%; transform: translate(-50%, -50%); display: flex; align-items: center; gap: 7px; font-size: 17.5px; white-space: nowrap; }
  .address svg { width: 13px; height: 16px; fill: var(--paper); }
  .band-wordmark { position: absolute; right: 62px; top: 50%; transform: translateY(-50%); font-size: 15px; font-weight: 500; letter-spacing: 1px; }

  /* Back */
  .card-back { top: 637px; background: var(--maroon-deep); color: var(--paper); }
  .wordmark { position: absolute; left: 100px; top: 176px; width: 252px; text-align: center; font-weight: 500; white-space: nowrap; }
  .wordmark-name { font-size: 46px; line-height: 1; letter-spacing: 2px; }
  .wordmark-sub { font-size: 27px; line-height: 1; margin-top: 44px; letter-spacing: 0.5px; }
  .services-rule { position: absolute; left: 389px; top: 75px; width: 1.5px; height: 278px; background: var(--rule-light); }
  .services { position: absolute; left: 428px; top: 67px; list-style: none; }
  .services li { position: relative; padding-left: 21px; height: 19.1px; line-height: 19.1px; font-size: 16px; white-space: nowrap; }
  .services li::before { content: ""; position: absolute; left: 2px; top: 6px; border-left: 9px solid var(--paper); border-top: 4px solid transparent; border-bottom: 4px solid transparent; }
</style>
</head>
<body>
  <section class="card card-front" aria-label="Business card front">
    <div class="identity">
      <p class="identity-name">DWAYNE HALSTER</p>
      <p class="identity-role">Owner</p>
    </div>
    <div class="identity-rule"></div>
    <ul class="contact-list">
      <li><svg viewBox="0 0 24 24"><path d="M6.6 10.8a15.1 15.1 0 0 0 6.6 6.6l2.2-2.2a1 1 0 0 1 1-.25 11.4 11.4 0 0 0 3.6.57 1 1 0 0 1 1 1V20a1 1 0 0 1-1 1A17 17 0 0 1 3 4a1 1 0 0 1 1-1h3.5a1 1 0 0 1 1 1c0 1.25.2 2.45.57 3.57a1 1 0 0 1-.25 1z"/></svg>(325) 482-5096</li>
      <li><svg viewBox="0 0 24 24"><path d="M2 5h20v14H2z M2 5l10 8 10-8" /></svg>info@corvaneconstruction.com</li>
      <li><svg viewBox="0 0 24 24"><circle cx="12" cy="12" r="10"/></svg>www.corvaneconstruction.com</li>
    </ul>
    <div class="address-band">
      <p class="address"><svg viewBox="0 0 24 30"><path d="M12 0a12 12 0 0 0-12 12c0 9 12 18 12 18s12-9 12-18A12 12 0 0 0 12 0zm0 17a5 5 0 1 1 0-10 5 5 0 0 1 0 10z"/></svg>4875 FM 309, Brackton, TX 79412</p>
      <p class="band-wordmark">CORVANE</p>
    </div>
  </section>

  <section class="card card-back" aria-label="Business card back">
    <div class="wordmark">
      <p class="wordmark-name">CORVANE</p>
      <p class="wordmark-sub">CONSTRUCTION</p>
    </div>
    <div class="services-rule"></div>
    <ul class="services">
      <li>Roads</li>
      <li>Substation Pads</li>
      <li>Temporary Pads</li>
      <li>Site Pads</li>
      <li>Land Leveling</li>
      <li>Powerline Row Cleaning</li>
      <li>Land Clearing</li>
      <li>Gates</li>
      <li>Fencing</li>
      <li>Construction Entrances</li>
      <li>Excavation</li>
      <li>Trenching</li>
      <li>Underground Utilities</li>
      <li>Directional Boring</li>
      <li>Pile Driving</li>
    </ul>
  </section>
</body>
</html>
```